Insert sheet for our Dog Food Package

We need an information sheet to go inn our pet food package, with branding, and information on ingredients, nutrition and feeding guidance. We will also need two additional items which will be a variation on the label design:
1) Label for package (detailed label about us and our food)
2) Label for outer shipping box (simple label for branding)
We will start with the information, insert page. The winning designer will then deliver the package and box labels as simplified versions of the same graphical theme.
I have attached samples of an earlier drafts of the insert piece. Please disregard the style, form and colors of the examples given. THEY ARE ONLY THERE TO SHOW WHAT INFORMATION SHOULD BE INCLUDED. All colors and style should be from our logo (attached). All graphics, font styles, and placement of elements need to be YOUR creative design - not a copy of the sample we gave. PLEASE READ THIS AND PLEASE DO NOT SUBMIT ANY VARIATION OF THE EXAMPLES!!!!!!!

Target Market(s)

Pet Owners

Industry/Entity Type

Pet Food

Colors
EB3D1F
EC4F4E
F09395
F8D3D4
FCEDEE

Requirements
Must have
• All new design. New colors (based in the palette of our logo), new graphics, new fonts, new placement of elements.
Should not have
• Please disregard the style, form and colors of the examples given. THEY ARE ONLY THERE TO SHOW WHAT INFORMATION SHOULD BE INCLUDED.

```html
<!DOCTYPE html>
<html lang="en">
<head>
<meta charset="utf-8">
<title>Vetra Insert Sheet</title>
<link href="https://fonts.googleapis.com/css2?family=Montserrat:wght@400;500;600;700;800;900&display=swap" rel="stylesheet">
<style>
  :root {
    --red: #a8231d;
    --red-bright: #b3261e;
    --brown: #4a1509;
    --ink: #2a1a16;
    --panel: #ececec;
    --white: #ffffff;
    --grass-dark: #3f7a12;
    --grass-light: #9fd34a;
  }
  * { box-sizing: border-box; margin: 0; padding: 0; }
  html, body { width: 711px; height: 1200px; overflow: hidden; background: #ffffff; }
  body { font-family: "Montserrat", Arial, sans-serif; color: var(--ink); }
  .sheet { position: relative; width: 711px; height: 1200px; background: var(--white); overflow: hidden; }

  .hero-disc { position: absolute; left: 0; top: 0; width: 711px; height: 520px; }
  .dog-photo {
    position: absolute; left: 425px; top: 62px; width: 262px; height: 510px;
    border-radius: 110px 110px 60px 60px;
    background: linear-gradient(180deg, #c9875a 0%, #e8d4c4 35%, #ffffff 62%, #eeeae7 100%);
  }

  .brand { position: absolute; left: 50px; top: 70px; display: flex; align-items: center; gap: 16px; }
  .brand-dot { width: 92px; height: 92px; border-radius: 50%; background: var(--red); }
  .brand-name { font-weight: 600; font-size: 50px; letter-spacing: 6px; color: var(--red); line-height: 1; }
  .brand-tag { display: flex; align-items: center; gap: 6px; margin-top: 8px; font-size: 12px; font-weight: 600; letter-spacing: 2px; color: var(--brown); }
  .brand-tag::before { content: ""; width: 64px; height: 2px; background: var(--brown); }

  .headline { position: absolute; left: 50px; top: 222px; line-height: 1; }
  .headline span { display: block; }
  .headline .l1 { font-weight: 900; font-size: 52px; color: var(--brown); }
  .headline .l2 { font-weight: 900; font-size: 56px; color: var(--red); margin-top: 8px; }
  .headline .l3 { font-weight: 600; font-size: 46px; color: var(--red); margin-top: 10px; letter-spacing: 1px; }

  .story { position: absolute; left: 48px; top: 430px; }
  .story h2 { font-size: 21px; font-weight: 700; color: var(--red); letter-spacing: .5px; }
  .story p { margin-top: 12px; padding-left: 16px; border-left: 3px solid var(--brown); font-size: 15px; font-weight: 500; line-height: 1.55; color: var(--ink); white-space: nowrap; }

  .mission { position: absolute; left: 46px; top: 600px; width: 623px; height: 123px; background: var(--red-bright); border-radius: 6px;
    color: var(--white); font-size: 13px; line-height: 1.55; text-align: center; padding: 20px 18px 0; }
  .mission::before { content: ""; position: absolute; left: 40px; right: 60px; top: -2px; height: 4px; background: var(--brown); border-radius: 2px; }

  .grass { position: absolute; left: 0; bottom: 0; width: 711px; height: 110px;
    background: linear-gradient(180deg, rgba(159,211,74,0) 0%, var(--grass-light) 40%, var(--grass-dark) 100%); }

  .divider { position: absolute; left: 356px; top: 755px; height: 390px; border-left: 2px dashed var(--brown); }

  .card { position: absolute; top: 753px; width: 287px; z-index: 2; }
  .card.nutrition { left: 46px; }
  .card.feeding { left: 380px; }
  .card-head { height: 56px; background: var(--brown); color: var(--white); border-radius: 14px 14px 0 0; font-size: 14.5px; font-weight: 700; display: flex; align-items: center; justify-content: center; }
  .card-body { margin-top: 6px; height: 316px; background: var(--panel); border: 2px solid var(--red); border-radius: 0 0 8px 8px; padding: 24px 18px 0; }
  .card-title { text-align: center; font-size: 14px; font-weight: 700; color: var(--red); letter-spacing: .5px; white-space: nowrap; }

  .stats { display: grid; grid-template-columns: 1fr 1.1fr; row-gap: 12px; margin-top: 24px; font-size: 14px; color: var(--red); font-weight: 500; white-space: nowrap; }
  .stats b { color: var(--brown); font-weight: 700; }
  .ingredients { margin-top: 20px; padding-top: 18px; border-top: 2px solid var(--brown); font-size: 10.5px; line-height: 1.7; color: var(--ink); white-space: nowrap; }

  .feed-table { width: 100%; margin-top: 24px; border-collapse: collapse; font-size: 12.5px; }
  .feed-table th { font-weight: 700; font-size: 12px; color: var(--ink); text-align: left; padding-bottom: 6px; border-bottom: 2px solid #8f8f8f; }
  .feed-table th:last-child, .feed-table td:last-child { text-align: right; }
  .feed-table td { color: var(--red); padding: 6px 0; font-weight: 500; }
  .feed-table tr.rule td { border-bottom: 1px solid #9a9a9a; }
</style>
</head>
<body>
<main class="sheet">
  <svg class="hero-disc" viewBox="0 0 711 520" aria-hidden="true">
    <circle cx="620" cy="225" r="240" fill="none" stroke="var(--brown)" stroke-width="12"/>
    <circle cx="620" cy="225" r="220" fill="var(--red-bright)"/>
  </svg>
  <div class="dog-photo" role="img" aria-label="Photo of a beagle puppy sitting and licking its nose"></div>

  <header class="brand">
    <div class="brand-dot"></div>
    <div>
      <div class="brand-name">VETRA</div>
      <div class="brand-tag">THE WHOLE HOUND</div>
    </div>
  </header>

  <h1 class="headline">
    <span class="l1">PREPARED</span>
    <span class="l2">WITH LOVE</span>
    <span class="l3">FOR MAPLE</span>
  </h1>

  <section class="story">
    <h2>OUR STORY</h2>
    <p>We Revolutionized the industry. Not<br>Formulated to meet a minimum standard,<br>but to develop the maximum<br>health of the whole dog.</p>
  </section>

  <p class="mission">We didn't just set about to create a food that will ‘pass a minimum standard’.<br>We set out to revolutionize the industry by creating a food that is designed with<br>Superfoods, Wholesome Grains, and Powerful Oils to help your dog achieve their maximum<br>health, happiness and longevity.</p>

  <div class="grass" role="img" aria-label="Photo of a strip of green grass along the bottom edge"></div>
  <div class="divider"></div>

  <section class="card nutrition">
    <div class="card-head">We prepared the best for Maple</div>
    <div class="card-body">
      <div class="card-title">NUTRITIONAL INFORMATION</div>
      <div class="stats">
        <span>Protein: <b>15%</b></span><span>Crude Fiber: <b>2.0%</b></span>
        <span>Total Fat: <b>9.5%</b></span><span>Moisture: <b>72%</b></span>
      </div>
      <p class="ingredients">Potassium Citrate, DiCalcium Phosphate,<br>Calcium Carbonate, Garbanzo Beans, Choline<br>Bitartrate, Taurine, Salt, Zinc Proteinate,<br>Magnesium Oxide, Iron Proteinate, Vitamin<br>B-12, Selenium, Niacin, Riboflavin, Calcium<br>Panthothen-ate, Thiamine, Vitamin A, Vitamin<br>D, Calcium Iodate, Vitamin B6, Folic Acid</p>
    </div>
  </section>

  <section class="card feeding">
    <div class="card-head">How much should i feed Maple?</div>
    <div class="card-body">
      <div class="card-title">RECOMMENDED FEEDING PLAN</div>
      <table class="feed-table">
        <thead><tr><th>APPROXIMATE WEIGHT</th><th>FULL MEAL</th></tr></thead>
        <tbody>
          <tr><td>&lt;20 lbs</td><td>110 g</td></tr>
          <tr><td>20-29 lbs</td><td>200 g</td></tr>
          <tr class="rule"><td>30-39 lbs</td><td>250 g</td></tr>
          <tr><td>40-54 lbs</td><td>300 g</td></tr>
          <tr><td>55-69 lbs</td><td>350 g</td></tr>
          <tr class="rule"><td>70-85 lbs</td><td>400 g</td></tr>
          <tr><td>85+ lbs</td><td>500 g</td></tr>
        </tbody>
      </table>
    </div>
  </section>
</main>
</body>
</html>
```